Unique Business Card Design

Unique Business Card design for our orthotic and prosthetic company. Our logo is on our website, color is light blue. Unique shape (artificial leg shaped, vertical, etc..) preferred. Logo, business name, individual name and basic demographics needed.

Industry/Entity Type

Business

Contact Information for Business Card

Logo, Industry, Phone # Logo, "Prosthetic & Orthotic Services" Place to add individual name and contact info

Colors
cee9f5

Requirements
Must have
• The icon must be there, placement of "Prosthetic & Orthotic Services" can be moved
Nice to have
• Like the mix of light blue, and a little darker blue. One design included the icons from my website which was a nice touch

```html
<!DOCTYPE html>
<html lang="en">
<head>
<meta charset="utf-8">
<title>Stridewell Inc. Business Card</title>
<link href="https://fonts.googleapis.com/css2?family=Open+Sans:wght@400;600;700&display=swap" rel="stylesheet">
<style>
  :root {
    --blue: #155ca8;
    --white: #ffffff;
    --swoosh: #4a4a4c;
    --backdrop: #e8ecec;
    --ink-soft: #eaf3fb;
  }
  * { margin: 0; padding: 0; box-sizing: border-box; }
  html, body { width: 1200px; height: 812px; overflow: hidden; }
  body {
    background: var(--backdrop);
    font-family: "Open Sans", Arial, sans-serif;
    position: relative;
  }
  .card {
    position: absolute;
    top: 258px;
    width: 520px;
    height: 297px;
    overflow: hidden;
  }
  .card--back { left: 50px; background: var(--blue); }
  .card--front { left: 630px; background: var(--white); }

  .back-emblem {
    position: absolute;
    left: 130px; top: 50px;
    width: 150px; height: 140px;
    border-radius: 50%;
    background: var(--white);
  }
  .back-url {
    position: absolute;
    left: 0; right: 0; top: 222px;
    text-align: center;
    color: var(--white);
    font-size: 14px;
    letter-spacing: 4px;
  }

  .front-shape { position: absolute; inset: 0; }

  .brand-dot {
    position: absolute;
    left: 38px; top: 78px;
    width: 76px; height: 76px;
    border-radius: 50%;
    background: var(--blue);
  }
  .brand {
    position: absolute;
    left: 130px; top: 70px;
    color: var(--blue);
  }
  .brand-name {
    font-size: 27px;
    font-weight: 700;
    letter-spacing: -0.5px;
    line-height: 1;
    padding-bottom: 5px;
    border-bottom: 2px solid var(--blue);
  }
  .brand-tagline {
    font-size: 13px;
    font-weight: 400;
    padding-top: 3px;
    padding-left: 20px;
  }

  .person {
    position: absolute;
    right: 280px; top: 200px;
    text-align: right;
    color: var(--white);
  }
  .person-name { font-size: 19px; font-weight: 700; line-height: 1.2; }
  .person-cred { font-size: 13px; font-weight: 600; line-height: 1.3; }
  .person-address { font-size: 13px; line-height: 1.4; margin-top: 6px; }

  .divider {
    position: absolute;
    left: 258px; top: 198px;
    width: 1px; height: 86px;
    background: var(--ink-soft);
    opacity: 0.7;
  }

  .contacts {
    position: absolute;
    left: 274px; top: 196px;
    list-style: none;
    color: var(--white);
    font-size: 13px;
    line-height: 21px;
  }
  .contacts li { display: flex; align-items: center; gap: 7px; }
  .contacts svg { width: 12px; height: 12px; flex: none; fill: var(--white); }
</style>
</head>
<body>

  <section class="card card--back" aria-label="Card back">
    <div class="back-emblem"></div>
    <p class="back-url">www.stridewellinc.com</p>
  </section>

  <section class="card card--front" aria-label="Card front">
    <svg class="front-shape" viewBox="0 0 520 297" preserveAspectRatio="none" aria-hidden="true">
      <path d="M0,186 C210,176 430,128 520,22 L520,297 L0,297 Z" fill="var(--blue)"/>
      <path d="M0,186 C210,172 420,118 512,14 L520,22 C430,128 210,176 0,186 Z" fill="var(--swoosh)"/>
    </svg>

    <div class="brand-dot"></div>
    <div class="brand">
      <div class="brand-name">STRIDEWELL INC.</div>
      <div class="brand-tagline">Prosthetic &amp; Orthotic Services</div>
    </div>

    <div class="person">
      <p class="person-name">Talia Brenner</p>
      <p class="person-cred">CO LPO</p>
      <p class="person-address">2280 Harbor Ave.<br>Fairview, NY 10090</p>
    </div>

    <div class="divider"></div>

    <ul class="contacts">
      <li>
        <svg viewBox="0 0 24 24" aria-hidden="true"><path d="M6.6 10.8c1.4 2.8 3.8 5.1 6.6 6.6l2.2-2.2c.3-.3.7-.4 1-.2 1.1.4 2.3.6 3.6.6.6 0 1 .4 1 1V20c0 .6-.4 1-1 1C10.6 21 3 13.4 3 4c0-.6.4-1 1-1h3.5c.6 0 1 .4 1 1 0 1.3.2 2.5.6 3.6.1.3 0 .7-.2 1z"/></svg>
        555.010.1700
      </li>
      <li>
        <svg viewBox="0 0 24 24" aria-hidden="true"><path d="M6 2h12v6H6zM3 9h18v9h-3v4H6v-4H3zm5 6v5h8v-5z"/></svg>
        555.010.3919
      </li>
      <li>
        <svg viewBox="0 0 24 24" aria-hidden="true"><path d="M7 1h10a2 2 0 0 1 2 2v18a2 2 0 0 1-2 2H7a2 2 0 0 1-2-2V3a2 2 0 0 1 2-2zm0 3v14h10V4z"/></svg>
        555-014-5415
      </li>
      <li>
        <svg viewBox="0 0 24 24" aria-hidden="true"><path d="M2 5h20v14H2zm2 2v.5l8 5 8-5V7z"/></svg>
        tbrenner@stridewellinc.com
      </li>
    </ul>
  </section>

</body>
</html>
```